Business Card for Multi-Brand Sportswear Company

We are looking for a business card which represents our company and the multiple brands within it.

The company: Fen Athletics (LTD)
The brands: Fen, TavaPuni, ElmStretch, Grit and Rain

Employees using these cards would be representing Fen Athletics, rather than any of the individual brands. You will see a current design within the uploaded files, to give some inspiration. The actual text of the brands is not necessary, but the logos should be on there is some format.

Our creative minds on this are stretched, so we are looking for someone to make this their own, and show us what a good business card should look like.

We may like to get these printed with spot gloss, so keep that in mind with your designs.

www.fenathletics.co.uk

Industry/Entity Type

Business

Contact Information for Business Card

Leo Pemberton-Hale
Operations Manager
(+44) 1632 960 418
Leo@fenathletics.co.uk
www.fenathletics.co.uk

Font styles to use
Sans Serif
Other font styles liked:
• Eurostile

Colors
ffffff

Requirements
Nice to have
• Dark (black) background

```html
<!DOCTYPE html>
<html lang="en">
<head>
<meta charset="utf-8">
<title>Fen Athletics – Business Card</title>
<link rel="stylesheet" href="https://fonts.googleapis.com/css2?family=Michroma&family=Montserrat:wght@500;600;700;800&display=swap">
<style>
  :root {
    --backdrop: #9c9a9b;
    --card: #1b1a1a;
    --white: #ffffff;
    --red: #e3232b;
    --grey: #8a8a8a;
    --divider: #4a4a4a;
  }
  * { margin: 0; padding: 0; box-sizing: border-box; }
  html, body { width: 1200px; height: 900px; overflow: hidden; }
  body {
    background: radial-gradient(ellipse at 50% 40%, #b3b1b2 0%, var(--backdrop) 70%);
    font-family: "Montserrat", Arial, sans-serif;
    position: relative;
  }
  .card {
    position: absolute;
    width: 560px;
    height: 320px;
    background: var(--card);
    border-radius: 30px;
    box-shadow: 0 12px 30px rgba(0,0,0,0.35);
    color: var(--white);
  }
  .card--front { left: 70px; top: 70px; }
  .card--back { left: 570px; top: 500px; }

  .holder { position: absolute; left: 0; right: 0; top: 92px; text-align: center; }
  .holder__name {
    font-family: "Michroma", "Arial Black", sans-serif;
    font-size: 34px;
    letter-spacing: 1px;
    line-height: 1;
  }
  .holder__role {
    margin-top: 6px;
    font-weight: 700;
    font-size: 17px;
    color: var(--red);
    letter-spacing: 0.5px;
  }
  .brand-row {
    position: absolute; left: 0; right: 0; top: 222px;
    display: flex; justify-content: center; gap: 28px;
    font-weight: 600; font-size: 13px; color: var(--grey);
    letter-spacing: 0.5px;
  }

  .wordmark {
    position: absolute; left: 44px; top: 126px;
    font-weight: 700; font-size: 34px; color: var(--grey);
    letter-spacing: 1px;
  }
  .divider {
    position: absolute; left: 298px; top: 110px;
    width: 1px; height: 78px; background: var(--divider);
  }
  .contact { position: absolute; left: 320px; top: 112px; list-style: none; }
  .contact li {
    display: flex; align-items: center; gap: 12px;
    font-weight: 600; font-size: 13px; height: 26px;
  }
  .contact svg, .address svg { width: 14px; height: 14px; flex: none; }
  .accent { color: var(--red); }
  .address {
    position: absolute; left: 0; right: 0; top: 262px;
    display: flex; justify-content: center; align-items: center; gap: 10px;
    font-weight: 600; font-size: 14px; letter-spacing: 0.3px;
  }
</style>
</head>
<body>

<section class="card card--front" aria-label="Business card front">
  <div class="holder">
    <p class="holder__name">OWEN MARSH</p>
    <p class="holder__role">Managing Director</p>
  </div>
  <div class="brand-row">
    <span>ElmStretch</span>
    <span>Grit and Rain</span>
    <span>Fen</span>
    <span>TavaPuni</span>
  </div>
</section>

<section class="card card--back" aria-label="Business card back">
  <p class="wordmark">Fen Athletics</p>
  <span class="divider"></span>
  <ul class="contact">
    <li>
      <svg viewBox="0 0 24 24" fill="var(--red)"><path d="M6.6 10.8a15 15 0 0 0 6.6 6.6l2.2-2.2a1 1 0 0 1 1-.25 11.4 11.4 0 0 0 3.6.57 1 1 0 0 1 1 1V20a1 1 0 0 1-1 1A17 17 0 0 1 3 4a1 1 0 0 1 1-1h3.5a1 1 0 0 1 1 1c0 1.25.2 2.45.57 3.6a1 1 0 0 1-.25 1z"/></svg>
      +44(0)1632960418
    </li>
    <li>
      <svg viewBox="0 0 24 24" fill="var(--red)"><path d="M2 5h20v14H2z"/><path d="M2 5l10 8 10-8" stroke="var(--card)" stroke-width="2" fill="none"/></svg>
      owen@fenathletics.co.uk
    </li>
    <li>
      <svg viewBox="0 0 24 24" fill="none" stroke="var(--red)" stroke-width="2"><circle cx="12" cy="12" r="9" fill="var(--red)"/><path d="M3 12h18M12 3c3 3 3 15 0 18M12 3c-3 3-3 15 0 18" stroke="var(--card)" stroke-width="1.4"/></svg>
      <span>www.<span class="accent">fenathletics</span>.co.uk</span>
    </li>
  </ul>
  <p class="address">
    <svg viewBox="0 0 24 24" fill="var(--red)"><path d="M12 2a7 7 0 0 0-7 7c0 5 7 13 7 13s7-8 7-13a7 7 0 0 0-7-7zm0 9.5A2.5 2.5 0 1 1 12 6.5a2.5 2.5 0 0 1 0 5z"/></svg>
    Alder Court, Marlow End, Fenby, FB42QT
  </p>
</section>

</body>
</html>
```